Fitness website

Website for a fitness brand (see attached specs). Design needs to be modern and vibrant with CTAs on every page. We will provide logos, images, etc but for now user placeholder text and images. For now use the name 'Corvane Athletics' as the name to use on the design. The goal of this site is to either get people to join the gym (5 physical locations across the US); buy an online program; buy merch or supplements or sign up for the newsletter. Pleas use images from this foldeR: https://filebarn.example/share/folders/8QwTz41mKpLrXv93NdYe7HsaBuJ0Cf2_R?usp=sharing

We will be coding this in ReactNative. Lots more work for the winner as well, this is a 1st project for us.

Target Market(s)

fitness enthusiats

Industry/Entity Type

fitness, health, wellness

Number of Pages Required

5+ page

Font styles to use
Other font styles liked:
• Lato

Colors
0054AA
0677BA
7BADD7
CADEEF
E8F1F8
0094D4
00A9DD
6FCCEA
C7EBF8
E9F6FB
00AB8E
00BBA5
67D7C9
C6EFE9
E9F9F6
EE7325
F08F49
F5BC92
FAE3D3
FDF4ED

Requirements
Must have
• must be reactive. most people will view it first on mobile
Nice to have
• video in hero section of top of home page

```html
<!DOCTYPE html>
<html lang="en">
<head>
<meta charset="utf-8">
<title>Corvane Athletics — Built for Performance</title>
<link rel="stylesheet" href="https://fonts.googleapis.com/css2?family=Barlow+Semi+Condensed:wght@500;600;700&family=Lato:wght@400;700&display=swap">
<style>
:root{
  --orange:#EE7325;
  --orange-soft:#F08F49;
  --blue:#0054AA;
  --blue-mid:#0677BA;
  --blue-pale:#7BADD7;
  --ink:#1b2030;
  --text:#3a3f4b;
  --line:#dfe3ea;
  --white:#fff;
  --head:"Barlow Semi Condensed",sans-serif;
  --body:"Lato",sans-serif;
}
*{box-sizing:border-box;margin:0;padding:0}
html,body{width:1200px;height:4983px;overflow:hidden}
body{position:relative;background:var(--white);font-family:var(--body);color:var(--text)}
.abs{position:absolute}
.btn{position:absolute;display:flex;align-items:center;justify-content:center;background:var(--orange);color:#fff;font-family:var(--head);font-weight:600;font-size:14px;letter-spacing:.5px;text-transform:uppercase;border-radius:22px}
.btn.square{border-radius:0}
.eyebrow{position:absolute;font-family:var(--head);font-weight:600;font-size:15px;color:var(--blue);text-transform:uppercase;letter-spacing:.4px}
.h2{position:absolute;font-family:var(--head);font-weight:700;color:var(--ink);text-transform:uppercase;line-height:1}

/* hero */
.hero{position:absolute;left:0;top:0;width:1200px;height:760px;overflow:hidden}
.hero-photo{position:absolute;inset:0;background:radial-gradient(ellipse at 55% 45%,#5a6270 0%,#2c323c 45%,#15181e 100%)}
.nav{position:absolute;left:0;top:0;width:1200px;height:85px;background:rgba(20,24,32,.55);border-bottom:1px solid rgba(255,255,255,.12)}
.brand{position:absolute;left:64px;top:30px;font-family:var(--head);font-weight:700;font-size:22px;color:#fff;letter-spacing:.3px}
.nav a{position:absolute;top:36px;font-family:var(--head);font-weight:600;font-size:13px;color:#fff;text-decoration:none;text-transform:uppercase}
.nav a.active::after{content:"";position:absolute;left:0;right:0;bottom:-9px;height:2px;background:#fff}
.nav .contact{top:24px;left:1006px;width:126px;height:36px;border:1.5px solid #fff;border-radius:18px;display:flex;align-items:center;justify-content:center}
.hero-kicker{position:absolute;left:0;width:1200px;top:244px;text-align:center;font-family:var(--head);font-weight:600;font-size:20px;color:#fff;letter-spacing:3px}
.hero-kicker::before{content:"";display:inline-block;width:42px;height:2px;background:var(--orange);vertical-align:middle;margin-right:12px}
.hero-title{position:absolute;left:0;width:1200px;top:274px;text-align:center;font-family:var(--head);font-weight:700;font-size:56px;line-height:60px;color:#fff;text-transform:uppercase}
.scroll-mark{position:absolute;left:577px;top:730px;width:46px;height:46px;background:#fff;transform:rotate(45deg);box-shadow:0 4px 14px rgba(0,0,0,.15)}

/* programs */
.card{position:absolute;width:318px;height:400px;background:#fff;border:1px solid var(--line);box-shadow:0 2px 10px rgba(0,0,0,.05)}
.card .pic{position:absolute;left:0;top:0;width:100%;height:222px}
.card svg.cut{position:absolute;left:0;top:196px}
.card .ico{position:absolute;left:136px;top:180px;width:46px;height:46px;border-radius:50%;background:var(--blue);border:3px solid #fff;display:flex;align-items:center;justify-content:center}
.card h3{position:absolute;left:0;right:0;top:236px;text-align:center;font-family:var(--head);font-weight:700;font-size:21px;color:var(--ink);text-transform:uppercase}
.card p{position:absolute;left:38px;right:38px;top:270px;text-align:center;font-size:13px;line-height:17px;color:var(--text)}
.card .btn{left:93px;top:331px;width:132px;height:36px;font-size:12px}
.card.featured{background:var(--blue);border-color:var(--blue);box-shadow:0 10px 24px rgba(0,84,170,.3)}
.card.featured h3,.card.featured p{color:#fff}
.card.featured .ico{background:var(--orange)}

/* about */
.about-photo{position:absolute;left:0;top:1838px;width:600px;height:620px;clip-path:polygon(0 0,425px 0,600px 310px,425px 620px,0 620px);background:linear-gradient(135deg,#4a4f58,#23272e 60%,#3b3f47)}
.about-copy{position:absolute;left:654px;top:2030px;width:490px;border-left:2px solid var(--orange);padding-left:16px;font-size:16px;line-height:26px;color:#333}
.stat{position:absolute;top:2210px}
.stat b{display:block;font-family:var(--head);font-weight:700;font-size:38px;color:var(--blue-mid);line-height:1}
.stat span{display:block;margin-top:6px;font-family:var(--head);font-weight:500;font-size:13px;color:#333;text-transform:uppercase}

/* shop */
.shop-band{position:absolute;left:0;top:2458px;width:1200px;height:464px;background:linear-gradient(100deg,#e86f22,#EE7325 45%,#f08a42)}
.product{position:absolute;top:2680px;width:232px;height:325px;background:linear-gradient(135deg,#fff 0%,#f1f2f4 100%);border:1px solid #e4e6ea;box-shadow:0 6px 18px rgba(0,0,0,.1)}
.product .pic{position:absolute;left:40px;top:22px;width:152px;height:168px;border-radius:6px;background:radial-gradient(circle at 50% 45%,#3c3f45,#9ea2a8 70%,transparent 72%)}
.product h4{position:absolute;left:0;right:0;top:222px;text-align:center;font-family:var(--head);font-weight:700;font-size:18px;color:var(--ink);text-transform:uppercase}
.product small{position:absolute;left:0;right:0;top:248px;text-align:center;font-size:9px;color:#555;text-transform:uppercase}
.product .price{position:absolute;left:0;right:0;top:266px;text-align:center;font-family:var(--head);font-weight:700;font-size:22px;color:var(--blue)}
.product .bar{position:absolute;left:76px;bottom:-1px;width:80px;height:3px;background:var(--blue)}
.product.active{border:2px solid var(--orange)}
.product.active .bar{display:none}
.product.active .dot{position:absolute;left:104px;bottom:-12px;width:22px;height:22px;border-radius:50%;background:var(--orange)}
.arrow-btn{position:absolute;top:3037px;width:44px;height:44px;border-radius:50%;display:flex;align-items:center;justify-content:center}

/* locations */
.loc{position:absolute;overflow:hidden}
.loc .label{position:absolute;left:22px;bottom:18px;font-family:var(--head);font-weight:700;font-size:21px;color:#fff;text-transform:uppercase}
.loc svg{position:absolute;right:16px;bottom:16px}

/* join */
.field{position:absolute;height:46px;border:1px solid #cfd4dc;background:#fff;font-size:14px;color:#333;padding:14px 0 0 18px}

/* footer */
.footer{position:absolute;left:0;top:4300px;width:1200px;height:683px;background:linear-gradient(180deg,#0b4fb2,#0a4aa8)}
.footer h5{position:absolute;font-family:var(--head);font-weight:700;font-size:21px;color:#fff;text-transform:uppercase}
.footer ul{position:absolute;list-style:none}
.footer li{font-size:14.5px;color:#fff;line-height:28px}
.footer li::before{content:"»";margin-right:8px}
</style>
</head>
<body>

<!-- HERO -->
<header class="hero">
  <div class="hero-photo" role="img" aria-label="Athlete skipping rope in a dark training arena"></div>
  <nav class="nav">
    <div class="brand">CORVANE ATHLETICS</div>
    <a class="active" style="left:297px">Home</a>
    <a style="left:372px">About Us</a>
    <a style="left:470px">Programs</a>
    <a style="left:577px">Shop</a>
    <a style="left:648px">Locations</a>
    <a style="left:755px">Affiliate</a>
    <a style="left:853px">Blog</a>
    <a style="left:923px">Members</a>
    <a class="contact">Contact &rsaquo;</a>
  </nav>
  <div class="hero-kicker">CORVANE ATHLETICS</div>
  <h1 class="hero-title">Built for Performance<br>Driven by Passion</h1>
  <a class="btn" style="left:517px;top:416px;width:172px;height:42px">Join the Gym &rsaquo;</a>
  <svg class="abs" style="left:0;top:600px" width="1200" height="160" viewBox="0 0 1200 160">
    <polygon points="0,38 600,118 1200,38 1200,68 600,135 0,68" fill="#EE7325"/>
    <polygon points="0,68 600,135 1200,68 1200,160 0,160" fill="#fff"/>
  </svg>
</header>
<div class="scroll-mark"></div>
<svg class="abs" style="left:589px;top:739px" width="22" height="28" viewBox="0 0 22 28"><rect x="4" y="2" width="14" height="22" rx="7" fill="none" stroke="#333" stroke-width="1.6"/><line x1="11" y1="7" x2="11" y2="11" stroke="#333" stroke-width="1.6"/></svg>

<!-- PROGRAMS -->
<h2 class="h2" style="left:0;width:1200px;text-align:center;top:840px;font-size:42px">Our Programs</h2>

<article class="card" style="left:112px;top:927px">
  <div class="pic" role="img" aria-label="Masters athlete training with weights" style="background:linear-gradient(135deg,#5b5f66,#2e3238)"></div>
  <svg class="cut" width="318" height="30"><polygon points="0,4 159,26 318,4 318,30 0,30" fill="#fff"/><polyline points="0,2 159,24 318,2" fill="none" stroke="#EE7325" stroke-width="4"/></svg>
  <div class="ico"><svg width="22" height="22" viewBox="0 0 24 24"><path d="M5 16c2-6 6-9 10-9l2 3-4 1c2 2 4 3 6 3" fill="none" stroke="#fff" stroke-width="2.4"/></svg></div>
  <h3>Masters</h3>
  <p>Lorem ipsum dolor sit amet consecte-tur adipiscing elit sed doLorem ipsum dolor sit amet consectetur</p>
  <a class="btn">Learn More &rsaquo;</a>
</article>
<article class="card featured" style="left:453px;top:927px">
  <div class="pic" role="img" aria-label="Athlete doing functional fitness training" style="background:linear-gradient(135deg,#6b6f76,#3a3e45)"></div>
  <svg class="cut" width="318" height="30"><polygon points="0,4 159,26 318,4 318,30 0,30" fill="#0054AA"/><polyline points="0,2 159,24 318,2" fill="none" stroke="#EE7325" stroke-width="4"/></svg>
  <div class="ico"><svg width="24" height="24" viewBox="0 0 24 24"><path d="M2 12h20M5 8v8M8 7v10M16 7v10M19 8v8" stroke="#fff" stroke-width="2.2" fill="none"/></svg></div>
  <h3>Functional Fitness</h3>
  <p>Lorem ipsum dolor sit amet consecte-tur adipiscing elit sed doLorem ipsum dolor sit amet consectetur</p>
  <a class="btn">Learn More &rsaquo;</a>
</article>
<article class="card" style="left:791px;top:927px">
  <div class="pic" role="img" aria-label="Competitive athletes lifting barbells overhead" style="background:linear-gradient(135deg,#4e535b,#262a30)"></div>
  <svg class="cut" width="318" height="30"><polygon points="0,4 159,26 318,4 318,30 0,30" fill="#fff"/><polyline points="0,2 159,24 318,2" fill="none" stroke="#EE7325" stroke-width="4"/></svg>
  <div class="ico"><svg width="22" height="22" viewBox="0 0 24 24"><path d="M7 4h10v5a5 5 0 0 1-10 0zM12 14v4M8 20h8" stroke="#fff" stroke-width="2.2" fill="none"/></svg></div>
  <h3>Competitive</h3>
  <p>Lorem ipsum dolor sit amet consecte-tur adipiscing elit sed doLorem ipsum dolor sit amet consectetur</p>
  <a class="btn">Learn More &rsaquo;</a>
</article>

<article class="card" style="left:112px;top:1362px">
  <div class="pic" role="img" aria-label="Athlete reviewing a nutrition plan" style="background:linear-gradient(135deg,#77736e,#3d3a37)"></div>
  <svg class="cut" width="318" height="30"><polygon points="0,4 159,26 318,4 318,30 0,30" fill="#fff"/><polyline points="0,2 159,24 318,2" fill="none" stroke="#EE7325" stroke-width="4"/></svg>
  <div class="ico"><svg width="22" height="22" viewBox="0 0 24 24"><path d="M12 7c-5-3-9 1-7 7 1 4 4 7 7 5 3 2 6-1 7-5 2-6-2-10-7-7zM12 7V3" stroke="#fff" stroke-width="2" fill="none"/></svg></div>
  <h3>Nutritions</h3>
  <p>Lorem ipsum dolor sit amet consecte-tur adipiscing elit sed doLorem ipsum dolor sit amet consectetur</p>
  <a class="btn">Learn More &rsaquo;</a>
</article>
<article class="card" style="left:453px;top:1362px">
  <div class="pic" role="img" aria-label="Athlete on a bench press in the gym" style="background:linear-gradient(135deg,#5f6268,#2d3035)"></div>
  <svg class="cut" width="318" height="30"><polygon points="0,4 159,26 318,4 318,30 0,30" fill="#fff"/><polyline points="0,2 159,24 318,2" fill="none" stroke="#EE7325" stroke-width="4"/></svg>
  <div class="ico"><svg width="22" height="22" viewBox="0 0 24 24"><rect x="6" y="4" width="12" height="16" rx="2" stroke="#fff" stroke-width="2" fill="none"/><path d="M9 9h6M9 13h6" stroke="#fff" stroke-width="2"/></svg></div>
  <h3>Speciality</h3>
  <p>Lorem ipsum dolor sit amet consecte-tur adipiscing elit sed doLorem ipsum dolor sit amet consectetur</p>
  <a class="btn">Learn More &rsaquo;</a>
</article>
<article class="card" style="left:791px;top:1362px">
  <div class="pic" role="img" aria-label="Athlete holding a weight plate for hybrid racing" style="background:linear-gradient(135deg,#3a3d43,#16181c)"></div>
  <svg class="cut" width="318" height="30"><polygon points="0,4 159,26 318,4 318,30 0,30" fill="#fff"/><polyline points="0,2 159,24 318,2" fill="none" stroke="#EE7325" stroke-width="4"/></svg>
  <div class="ico"><svg width="22" height="22" viewBox="0 0 24 24"><path d="M8 8a4 4 0 0 1 8 0l3 12H5z" stroke="#fff" stroke-width="2" fill="none"/></svg></div>
  <h3>Hybrid Race</h3>
  <p>Lorem ipsum dolor sit amet consecte-tur adipiscing elit sed doLorem ipsum dolor sit amet consectetur</p>
  <a class="btn">Learn More &rsaquo;</a>
</article>

<!-- ABOUT -->
<div class="about-photo" role="img" aria-label="Athletes training hard on air bikes"></div>
<div class="eyebrow" style="left:654px;top:1893px;font-size:13px">Built for athletes. Designed for everyone.</div>
<h2 class="h2" style="left:654px;top:1922px;font-size:42px;line-height:42px">About Corvane<br>Athletics</h2>
<p class="about-copy">Corvane Athletics is more than a gym — it's a movement. With 5 state-of-the-art training centers across the U.S. and a powerful online coaching platform, we help athletes and everyday warriors reach their next level. Whether you want to build strength, improve endurance, or transform your lifestyle — we've got your back.</p>
<div class="stat" style="left:654px"><b>50K+</b><span>Athletes Trained</span></div>
<div class="stat" style="left:818px"><b>4.8</b><span>Positive Rating</span></div>
<div class="stat" style="left:973px"><b>97%</b><span>Result Satisfaction</span></div>
<a class="btn square" style="left:648px;top:2300px;width:166px;height:40px;font-size:13px">Learn More &rsaquo;</a>

<!-- SHOP -->
<div class="abs" style="left:600px;top:2428px;width:2px;height:30px;background:var(--orange)"></div>
<section class="shop-band" role="img" aria-label="Athletes training, faded behind orange tint"></section>
<div class="abs" style="left:0;width:1200px;top:2556px;text-align:center;font-family:var(--head);font-weight:600;font-size:14px;color:#1b2a55;text-transform:uppercase">Buy merch or supplements</div>
<h2 class="h2" style="left:0;width:1200px;text-align:center;top:2582px;font-size:40px;color:#fff">Shop Corvane</h2>

<div class="product" style="left:97px"><div class="pic" role="img" aria-label="Supplement bottle"></div><h4>Product Heading</h4><small>Lorem ipsum is simply dum</small><div class="price">$59.99</div><div class="bar"></div></div>
<div class="product active" style="left:350px"><div class="pic" role="img" aria-label="White supplement pouch" style="background:radial-gradient(circle at 50% 45%,#fafafa,#d6d8dc 70%,transparent 72%)"></div><h4>Product Heading</h4><small>Lorem ipsum is simply dum</small><div class="price">$59.99</div><div class="dot"></div></div>
<div class="product" style="left:606px"><div class="pic" role="img" aria-label="Black branded t-shirt and cap" style="background:radial-gradient(circle at 50% 45%,#111,#333 65%,transparent 68%)"></div><h4>Product Heading</h4><small>Lorem ipsum is simply dum</small><div class="price">$59.99</div><div class="bar"></div></div>
<div class="product" style="left:859px"><div class="pic" role="img" aria-label="Protein powder tub" style="background:radial-gradient(circle at 50% 45%,#5a6068,#a9adb3 68%,transparent 70%)"></div><h4>Product Heading</h4><small>Lorem ipsum is simply dum</small><div class="price">$59.99</div><div class="bar"></div></div>

<div class="arrow-btn" style="left:551px;background:var(--blue)"><svg width="20" height="20" viewBox="0 0 20 20"><path d="M16 10H4M9 5l-5 5 5 5" stroke="#fff" stroke-width="2.2" fill="none"/></svg></div>
<div class="arrow-btn" style="left:603px;background:var(--orange)"><svg width="20" height="20" viewBox="0 0 20 20"><path d="M4 10h12M11 5l5 5-5 5" stroke="#fff" stroke-width="2.2" fill="none"/></svg></div>

<!-- LOCATIONS -->
<div class="eyebrow" style="left:120px;top:3140px;font-size:17px">Join our gym</div>
<h2 class="h2" style="left:120px;top:3166px;font-size:42px">Our Location</h2>
<div class="abs" style="left:441px;top:3185px;width:654px;height:1px;background:var(--blue-pale)"></div>
<div class="abs" style="left:441px;top:3182px;width:7px;height:7px;border-radius:50%;background:var(--blue-pale)"></div>

<div class="loc" style="left:120px;top:3245px;width:321px;height:193px;background:linear-gradient(180deg,#8fa6c4,#b49a78 60%,#3d3a36)" role="img" aria-label="Boston skyline"><span class="label">Boston</span><svg width="26" height="26" viewBox="0 0 26 26"><path d="M13 2l11 11-11 11L2 13z" fill="none" stroke="#fff" stroke-width="1.3"/><path d="M8 13h10M14 9l4 4-4 4" stroke="#fff" stroke-width="1.3" fill="none"/></svg></div>
<div class="loc" style="left:449px;top:3245px;width:321px;height:397px;background:linear-gradient(180deg,#c79a86,#9b7e7a 40%,#4f4c55 80%,#2a2b31)" role="img" aria-label="Miami skyline at sunset"><span class="label">Miami</span><svg width="26" height="26" viewBox="0 0 26 26"><path d="M13 2l11 11-11 11L2 13z" fill="none" stroke="#fff" stroke-width="1.3"/><path d="M8 13h10M14 9l4 4-4 4" stroke="#fff" stroke-width="1.3" fill="none"/></svg></div>
<div class="loc" style="left:782px;top:3245px;width:323px;height:193px;background:linear-gradient(180deg,#a7bdd6,#d1a784 55%,#463f3a)" role="img" aria-label="Seattle skyline"><span class="label">Seattle</span><svg width="26" height="26" viewBox="0 0 26 26"><path d="M13 2l11 11-11 11L2 13z" fill="none" stroke="#fff" stroke-width="1.3"/><path d="M8 13h10M14 9l4 4-4 4" stroke="#fff" stroke-width="1.3" fill="none"/></svg></div>
<div class="loc" style="left:120px;top:3448px;width:321px;height:194px;background:linear-gradient(180deg,#5e6c8c,#2f3550 55%,#141826)" role="img" aria-label="San Diego skyline at dusk"><span class="label">San Diego</span><svg width="26" height="26" viewBox="0 0 26 26"><path d="M13 2l11 11-11 11L2 13z" fill="none" stroke="#fff" stroke-width="1.3"/><path d="M8 13h10M14 9l4 4-4 4" stroke="#fff" stroke-width="1.3" fill="none"/></svg></div>
<div class="loc" style="left:782px;top:3448px;width:323px;height:194px;background:linear-gradient(180deg,#b5c3d4,#6e7d6a 50%,#3f4a3a)" role="img" aria-label="Washington DC aerial view"><span class="label">DC</span><svg width="26" height="26" viewBox="0 0 26 26"><path d="M13 2l11 11-11 11L2 13z" fill="none" stroke="#fff" stroke-width="1.3"/><path d="M8 13h10M14 9l4 4-4 4" stroke="#fff" stroke-width="1.3" fill="none"/></svg></div>

<!-- JOIN -->
<svg class="abs" style="left:81px;top:3735px" width="540" height="540" viewBox="0 0 540 540" role="img" aria-label="Athletes lifting barbells and a runner in training">
  <defs>
    <linearGradient id="gymTone" x1="0" y1="0" x2="1" y2="1"><stop offset="0" stop-color="#5a5e66"/><stop offset="1" stop-color="#2a2d33"/></linearGradient>
    <linearGradient id="runTone" x1="0" y1="0" x2="1" y2="1"><stop offset="0" stop-color="#7d8088"/><stop offset="1" stop-color="#3b3e44"/></linearGradient>
  </defs>
  <polygon points="220,11 441,139 441,395 220,522 0,395 0,139" fill="#0054AA"/>
  <polygon points="220,29 425,148 425,386 220,504 16,386 16,148" fill="url(#gymTone)"/>
  <polygon points="418,270 520,329 520,447 418,506 316,447 316,329" fill="#fff"/>
  <polygon points="418,280 511,334 511,442 418,496 325,442 325,334" fill="url(#runTone)"/>
</svg>
<div class="eyebrow" style="left:660px;top:3807px;font-size:17px;font-weight:500;color:var(--blue-mid)">Get started now</div>
<h2 class="h2" style="left:660px;top:3834px;font-size:40px;line-height:43px">Join the Gym &amp; Buy<br>Our Online Program</h2>
<p class="abs" style="left:660px;top:3940px;width:420px;font-size:13.5px;line-height:20px;color:#333">Lorem ipsum dolor sit amet, consectetur adipiscing elit, sed do eiusmod tempor incididunt ut labore et dolore</p>
<div class="field" style="left:664px;top:4002px;width:193px">Name</div>
<div class="field" style="left:869px;top:4002px;width:193px">Email</div>
<div class="field" style="left:664px;top:4064px;width:193px">Phone</div>
<div class="field" style="left:869px;top:4064px;width:193px">Location</div>
<a class="btn square" style="left:668px;top:4133px;width:394px;height:47px;font-size:14px">Send Message &rsaquo;</a>

<!-- NEWSLETTER + FOOTER -->
<footer class="footer">
  <svg class="abs" style="left:0;top:0" width="1200" height="125" viewBox="0 0 1200 125">
    <polygon points="0,0 1200,0 1200,105 600,12 0,105" fill="#fff"/>
    <polygon points="0,105 600,12 1200,105 1200,122 600,24 0,122" fill="#EE7325"/>
  </svg>
  <div class="abs" style="left:0;width:1200px;top:100px;text-align:center;font-family:var(--head);font-weight:500;font-size:18px;color:#fff">STAY FIT. STAY CONNECTED.</div>
  <h2 class="h2" style="left:0;width:1200px;text-align:center;top:132px;font-size:42px;color:#fff">Join Our Newsletter</h2>
  <div class="abs" style="left:296px;top:199px;width:612px;height:50px;background:#fff;padding:16px 0 0 28px;font-size:14px;color:#222">Email address</div>
  <a class="btn square" style="left:767px;top:205px;width:134px;height:38px;font-size:13px">Subscribe &rsaquo;</a>

  <div class="abs" style="left:120px;top:345px;width:210px;text-align:center;font-family:var(--head);font-weight:700;font-size:38px;line-height:42px;color:#fff">CORVANE<br>ATHLETICS</div>
  <div class="abs" role="img" aria-label="Social link" style="left:166px;top:439px;width:26px;height:26px;border-radius:50%;background:var(--orange)"></div>
  <div class="abs" role="img" aria-label="Social link" style="left:204px;top:439px;width:26px;height:26px;border-radius:50%;background:#fff"></div>
  <div class="abs" role="img" aria-label="Social link" style="left:242px;top:439px;width:26px;height:26px;border-radius:50%;background:#fff"></div>

  <h5 style="left:400px;top:346px">Navigation</h5>
  <ul style="left:400px;top:384px"><li>Home</li><li>About Us</li><li>Programs</li><li>Shop</li><li>Locations</li></ul>
  <ul style="left:530px;top:384px"><li>Affiliate</li><li>Blog</li><li>Members</li><li>Contact Us</li></ul>

  <h5 style="left:695px;top:346px">Programs</h5>
  <ul style="left:693px;top:384px"><li>Masters</li><li>Functional Fitness</li><li>Competitive</li><li>Nutrition</li><li>Speciality</li><li>Hybrid Race</li></ul>

  <h5 style="left:888px;top:346px">Contact Us</h5>
  <svg class="abs" style="left:893px;top:394px" width="22" height="22" viewBox="0 0 24 24"><path d="M6 3l4 4-2 3c1 2 3 4 5 5l3-2 4 4-3 3C10 20 4 14 3 6z" fill="#fff"/></svg>
  <div class="abs" style="left:930px;top:396px;font-size:14.5px;color:#fff">+1 (555) 310-4820</div>
  <svg class="abs" style="left:893px;top:444px" width="24" height="18" viewBox="0 0 24 18"><rect x="1" y="1" width="22" height="16" fill="#fff"/><path d="M1 1l11 9 11-9" stroke="#0a4aa8" stroke-width="1.6" fill="none"/></svg>
  <div class="abs" style="left:930px;top:444px;font-size:14.5px;color:#fff">info@corvaneathletics.com</div>

  <div class="abs" style="left:120px;top:596px;width:970px;border-top:1px dashed rgba(255,255,255,.45)"></div>
  <div class="abs" style="left:1088px;top:581px;width:30px;height:30px;border-radius:50%;background:var(--orange);display:flex;align-items:center;justify-content:center"><svg width="14" height="14" viewBox="0 0 14 14"><path d="M3 9l4-4 4 4" stroke="#fff" stroke-width="2" fill="none"/></svg></div>
  <div class="abs" style="left:0;width:1200px;top:618px;text-align:center;font-size:12.5px;color:#fff">Copyright © 2025 Corvane Athletics. All Right Reserved</div>
</footer>

</body>
</html>
```